Modern Business Card for Larkwell 2018

Our company assumes the best about people. We are creating an online community of entrepreneurs and business leaders who struggle with marketing their business online.

This business card should POP! We recently got a new logo and are launching a new website next month, so our business cards should make a statement that feels:
-Fresh
-Smart
-Trustworthy
-Fun

Target Market(s)

small business owners, entrepreneurs

Industry/Entity Type

Digital Marketing

Contact Information for Business Card

Dimensions: 3.5" x 2"

Font styles to use
Sans Serif

Colors
f37122
ffffff

Requirements
Must have
• We need a business card with a modern, bold design. We will use one side of the card as a lead-generation offer, so text on one side will need to fit up to 140 characters. The business card should stick to our core colors (orange, black, and white).
Nice to have
• We think a vertical "portrait" design could be interesting.
Should not have
• Should not look like a traditional business card. The round icon should stand out from a distance.

```html
<!DOCTYPE html>
<html lang="en">
<head>
<meta charset="utf-8">
<title>Larkwell Business Card</title>
<link href="https://fonts.googleapis.com/css2?family=Roboto:wght@400;500;700&family=Roboto+Condensed:wght@500;700&display=swap" rel="stylesheet">
<style>
  :root {
    --orange: #e9612a;
    --white: #ffffff;
    --card-white: #f1f1f1;
    --ink: #1b1b1b;
    --backdrop: #e2e2e2;
  }
  html, body {
    margin: 0;
    width: 1200px;
    height: 960px;
    overflow: hidden;
    background: var(--backdrop);
    font-family: "Roboto", Arial, sans-serif;
  }
  .canvas { position: relative; width: 1200px; height: 960px; }
  .card {
    position: absolute;
    width: 600px;
    height: 343px;
    overflow: hidden;
    box-shadow: 0 4px 14px rgba(0,0,0,0.18);
  }
  /* Front */
  .card-front { left: 302px; top: 118px; background: var(--card-white); }
  .brand-tab {
    position: absolute; left: 0; top: 136px;
    width: 135px; height: 67px;
    background: var(--ink);
    border-radius: 0 34px 34px 0;
  }
  .brand-dot {
    position: absolute; left: 79px; top: 10px;
    width: 48px; height: 48px; border-radius: 50%;
    background: var(--orange);
  }
  .contact { position: absolute; left: 172px; top: 146px; }
  .contact-name {
    font-family: "Roboto Condensed", "Arial Narrow", sans-serif;
    font-weight: 500; font-size: 25px; color: var(--orange);
    letter-spacing: 0.2px;
  }
  .contact-role { font-weight: 500; font-size: 16px; color: var(--ink); margin-left: 8px; }
  .contact-dash { color: var(--orange); font-weight: 700; font-size: 20px; margin-left: 8px; }
  .contact-email { font-size: 15px; color: var(--ink); margin-top: 1px; }
  /* Back */
  .card-back { left: 299px; top: 499px; background: var(--orange); color: var(--white); }
  .brand-block { position: absolute; left: 30px; top: 57px; width: 258px; text-align: center; }
  .brand-circle {
    width: 38px; height: 38px; border-radius: 50%;
    background: var(--white); margin: 0 auto 10px;
  }
  .brand-name { font-weight: 700; font-size: 37px; letter-spacing: 1px; line-height: 1; }
  .brand-tagline {
    font-family: "Roboto Condensed", "Arial Narrow", sans-serif;
    font-weight: 700; font-size: 12px; letter-spacing: 1px;
    text-transform: uppercase; margin-top: 6px;
  }
  .divider {
    position: absolute; left: 297px; top: 26px;
    width: 1px; height: 165px; background: rgba(255,255,255,0.55);
  }
  .offer { position: absolute; left: 323px; top: 28px; width: 250px; }
  .offer-headline { font-weight: 700; font-size: 18.5px; line-height: 21px; text-transform: uppercase; margin: 0; }
  .offer-text { font-size: 15px; line-height: 19px; margin: 4px 0 0; }
  .offer-url { font-weight: 700; font-size: 19px; margin-top: 10px; }
  .note-box {
    position: absolute; left: 20px; top: 217px;
    width: 557px; height: 102px;
    background: var(--card-white); border-radius: 18px;
  }
  .note-line { position: absolute; left: 24px; width: 506px; height: 1px; background: var(--ink); }
  .note-line-1 { top: 31px; }
  .note-line-2 { top: 70px; }
</style>
</head>
<body>
<main class="canvas">
  <section class="card card-front" aria-label="Card front">
    <div class="brand-tab"><div class="brand-dot"></div></div>
    <div class="contact">
      <div><span class="contact-name">DANA WHITFORD</span><span class="contact-dash">-</span><span class="contact-role">Story Marketing Coach</span></div>
      <div class="contact-email">dana@larkwellnow.com</div>
    </div>
  </section>

  <section class="card card-back" aria-label="Card back">
    <div class="brand-block">
      <div class="brand-circle"></div>
      <div class="brand-name">LARKWELL</div>
      <div class="brand-tagline">Tell stories that inspire action</div>
    </div>
    <div class="divider"></div>
    <div class="offer">
      <p class="offer-headline">Reach more people.<br>Make more money.<br>Create more impact.</p>
      <p class="offer-text">Get your free Larkwell<br>Starter Package and our<br>marketing guide today at</p>
      <div class="offer-url">Larkwellnow.com/start</div>
    </div>
    <div class="note-box">
      <div class="note-line note-line-1"></div>
      <div class="note-line note-line-2"></div>
    </div>
  </section>
</main>
</body>
</html>
```